Visitenkarte für Ergotherapiepraxis
Zielgruppe
Wir arbeiten mit Kindern und Erwachsene jeden Alters.
Diese Personen kommen mit Beeinträchtigungen (körperlich, seelisch, schulisch) im täglichen Leben zu uns. Wir unterstützen unsere Patienten die Beeinträchtigungen zu verringern oder zu kompensieren und so den Alltag besser bewältigen zu können.
Aufgabenstellung
Ein Design was Kinder und Erwachsene anspricht, aber nicht zu verspielt wirkt. Es soll vertrauenserweckend sein. Eventuell sollte die Visitenkarte ein "aufgehendes oder erblühendes oder aufsteigendes" Element enthalten (=zu Beginn war die Beeinträchtigung dann steigt die Lebensqualität als Folge der Behandlung)
Daten vorn:
Ergotherapiepraxis

```html
<!DOCTYPE html>
<html lang="de">
<head>
<meta charset="utf-8">
<title>Visitenkarte Ergotherapiepraxis</title>
<link rel="stylesheet" href="https://fonts.googleapis.com/css2?family=PT+Sans:wght@400;700&family=PT+Sans+Narrow:wght@700&display=swap">
<style>
  :root {
    --backdrop: #333333;
    --teal: #00a99a;
    --teal-deep: #007f73;
    --paper: #ffffff;
    --ink: #4a4a4a;
    --text-font: "PT Sans", sans-serif;
    --head-font: "PT Sans Narrow", sans-serif;
  }
  * { margin: 0; padding: 0; box-sizing: border-box; }
  html, body { width: 918px; height: 1200px; overflow: hidden; }
  body { background: var(--backdrop); position: relative; font-family: var(--text-font); }

  .card {
    position: absolute; left: 58px; width: 804px; height: 521px;
    overflow: hidden; background: var(--paper);
    box-shadow: 0 3px 10px rgba(0,0,0,.45);
  }
  .card--front { top: 54px; }
  .card--back { top: 627px; }

  .band { position: absolute; left: 0; width: 100%; }
  .band--top { top: 0; height: 77px; background: linear-gradient(to bottom, var(--teal-deep), var(--teal)); }
  .band--middle { top: 347px; height: 82px; background: var(--teal); }
  .band--foot { top: 491px; height: 30px; background: linear-gradient(to bottom, var(--teal), var(--teal-deep)); }
  .band--bottom { top: 347px; height: 174px; background: linear-gradient(to bottom, var(--teal), var(--teal-deep)); }

  .disc { position: absolute; width: 354px; height: 354px; border-radius: 50%; background: var(--paper); }
  .card--front .disc { left: 7px; top: 41px; }
  .card--back .disc { left: 494px; top: 39px; }

  .artwork { position: absolute; border-radius: 40px; }
  .artwork--rising { left: 37px; top: 123px; width: 284px; height: 182px;
    background: linear-gradient(120deg, var(--teal) 0%, #8fd3cb 45%, #5a5a5a 100%); opacity: .85; }
  .artwork--butterfly { left: 482px; top: 86px; width: 229px; height: 246px; border-radius: 48% 52% 40% 60%;
    background: radial-gradient(circle at 45% 50%, var(--teal) 55%, #7fd2c9 100%); }

  .practice { position: absolute; left: 396px; top: 168px; }
  .practice__type { font-family: var(--head-font); font-weight: 700; color: var(--teal); font-size: 34px; line-height: 40px; }
  .practice__name { color: var(--ink); font-size: 35px; line-height: 42px; letter-spacing: -0.5px; }
  .practice__phone { color: var(--ink); font-size: 25px; line-height: 30px; margin-top: 18px; }

  .address { position: absolute; left: 0; top: 429px; width: 100%; height: 62px;
    display: flex; justify-content: center; align-items: center; gap: 30px;
    color: var(--ink); font-size: 25px; }

  .therapist { position: absolute; left: 21px; top: 205px; }
  .therapist__role { font-family: var(--head-font); font-weight: 700; color: var(--teal); font-size: 40px; line-height: 46px; letter-spacing: -0.5px; }
  .therapist__name { color: var(--ink); font-size: 35px; line-height: 46px; letter-spacing: -0.5px; }
</style>
</head>
<body>
  <section class="card card--front">
    <div class="band band--top"></div>
    <div class="band band--middle"></div>
    <div class="band band--foot"></div>
    <div class="disc"></div>
    <div class="artwork artwork--rising" role="img" aria-label="Illustration: Raupe mit aufsteigendem Pfeil und Rankenornament"></div>
    <div class="practice">
      <p class="practice__type">Ergotherapiepraxis</p>
      <p class="practice__name">Jana Brenner</p>
      <p class="practice__phone">Tel. 030512 / 48810</p>
    </div>
    <p class="address"><span>Am Lindenweg 4</span><span>|</span><span>15230 Kleinau, OT Heide</span></p>
  </section>

  <section class="card card--back">
    <div class="band band--top"></div>
    <div class="band band--bottom"></div>
    <div class="disc"></div>
    <div class="artwork artwork--butterfly" role="img" aria-label="Illustration: türkiser Schmetterling"></div>
    <div class="therapist">
      <p class="therapist__role">Behandelnder Therapeut</p>
      <p class="therapist__name">Jana Brenner</p>
    </div>
  </section>
</body>
</html>
```